Velmora Cabinets Letter Head and Email Signature

Hi
I would love a design package for a letterhead, email signature, even update my business card if you like if you can come up with a great idea for my new high end cabinet shop. Velmora Cabinets brings timeless craftsmanship to modern interiors, specializing in high end, custom cabinetry designed for architects and interior designers.

Target Market(s)

high end, luxury market

Industry/Entity Type

cabinet making

Requirements
Must have
• my colours of logo as the theme

```html
<!DOCTYPE html>
<html lang="en">
<head>
<meta charset="utf-8">
<title>Velmora Cabinets – Letterhead and Email Signature</title>
<link href="https://fonts.googleapis.com/css2?family=Montserrat:wght@400;500;700&family=PT+Sans:wght@400&display=swap" rel="stylesheet">
<style>
  :root {
    --backdrop: #b0b0b0;
    --paper: #ffffff;
    --brand-green: #2e7a3d;
    --signature-green: #4b7b40;
    --bar-green: #1f7a42;
    --ink: #1a1a1a;
    --body-grey: #555555;
    --rule-green: #3d7a3a;
  }
  * { margin: 0; padding: 0; box-sizing: border-box; }
  html, body { width: 1200px; height: 795px; overflow: hidden; }
  body {
    background: var(--backdrop);
    position: relative;
    font-family: "PT Sans", sans-serif;
  }

  /* ---------- Letterhead ---------- */
  .letterhead {
    position: absolute;
    left: 160px; top: 137px;
    width: 369px; height: 521px;
    background: var(--paper);
  }
  .letterhead .brand-name {
    position: absolute;
    left: 35px; top: 22px;
    font-family: "Montserrat", sans-serif;
    font-weight: 500;
    color: var(--brand-green);
    font-size: 13px;
    line-height: 15px;
    letter-spacing: 0.5px;
  }
  .letterhead .contact-rule {
    position: absolute;
    left: 227px; top: 24px;
    width: 1px; height: 25px;
    background: var(--rule-green);
  }
  .letterhead .contact-list {
    position: absolute;
    left: 237px; top: 22px;
    list-style: none;
    font-family: "Montserrat", sans-serif;
    font-size: 6.4px;
    line-height: 9.1px;
    color: var(--ink);
  }
  .contact-list li { display: flex; align-items: center; }
  .contact-list svg { fill: var(--brand-green); flex: none; }
  .letterhead .contact-list svg { width: 5px; height: 5px; margin-right: 3px; }

  .recipient {
    position: absolute;
    left: 35px; top: 122px;
    color: var(--body-grey);
  }
  .recipient .recipient-name { font-size: 7px; line-height: 10px; }
  .recipient .recipient-detail { font-size: 5.4px; line-height: 9px; }

  .letter-body {
    position: absolute;
    left: 35px; top: 185px;
    width: 299px;
    font-size: 5.3px;
    line-height: 9.1px;
    color: var(--body-grey);
    text-align: justify;
  }
  .letter-body p + p { margin-top: 8px; }

  .closing {
    position: absolute;
    left: 35px; top: 385px;
    color: var(--body-grey);
    font-size: 6px;
  }
  .closing .sender-name {
    margin-top: 22px;
    font-size: 7px;
  }

  .footer-bar-dark {
    position: absolute;
    left: 0; bottom: 0;
    width: 35px; height: 10px;
    background: var(--ink);
  }
  .footer-bar-green {
    position: absolute;
    left: 38px; right: 0; bottom: 0;
    height: 10px;
    background: var(--bar-green);
  }

  /* ---------- Email signature ---------- */
  .email-signature {
    position: absolute;
    left: 587px; top: 316px;
    width: 454px; height: 164px;
    background: var(--paper);
  }
  .email-signature .brand-name {
    position: absolute;
    left: 40px; top: 62px;
    font-family: "Montserrat", sans-serif;
    font-weight: 500;
    color: var(--brand-green);
    font-size: 19px;
    line-height: 22px;
    letter-spacing: 0.6px;
  }
  .email-signature .signature-rule {
    position: absolute;
    left: 227px; top: 36px;
    width: 1px; height: 91px;
    background: var(--rule-green);
  }
  .signature-details {
    position: absolute;
    left: 250px; top: 32px;
    font-family: "Montserrat", sans-serif;
  }
  .signature-details .person-name {
    font-size: 17.5px;
    font-weight: 700;
    color: var(--signature-green);
    line-height: 22px;
  }
  .signature-details .person-title {
    font-size: 10.5px;
    color: var(--ink);
    line-height: 14px;
  }
  .signature-details .contact-list {
    list-style: none;
    margin-top: 17px;
    font-size: 10.5px;
    line-height: 15.7px;
    color: var(--ink);
  }
  .signature-details .contact-list svg { width: 9px; height: 9px; margin-right: 5px; }
</style>
</head>
<body>

<section class="letterhead">
  <div class="brand-name">Velmora<br>Cabinets</div>
  <div class="contact-rule"></div>
  <ul class="contact-list">
    <li><svg viewBox="0 0 10 10"><path d="M1 3c0-1.5 1.5-2 4-2s4 .5 4 2v1H7V3H3v1H1zM2.5 5h5l1 4h-7z"/></svg>0412555309</li>
    <li><svg viewBox="0 0 10 10"><path d="M0 2h10v6H0z M0 2l5 3.5L10 2" stroke="#fff" stroke-width=".8"/></svg>info@velmoracabinets.com.au</li>
    <li><svg viewBox="0 0 10 10"><circle cx="5" cy="5" r="4"/></svg>@velmora.cabinets</li>
  </ul>

  <div class="recipient">
    <p class="recipient-name">MIRIAM CALLOWAY</p>
    <p class="recipient-detail">Chief Executive Officer</p>
    <p class="recipient-detail">City/State, Zip Code</p>
  </div>

  <div class="letter-body">
    <p>Proin gravida nibh vel velit auctor aliquet. Aenean sollicitudin, lorem quis bibendum auctor, nisi elit consequat ipsum, nec sagittis sem nibh id elit. Duis sed odio sit amet nibh vulputate cursus a sit amet mauris. Morbi accumsan ipsum velit. Nam nec tellus a odio tincidunt auctor a ornare odio. Sed non mauris vitae erat consequat auctor eu in elit. Class aptent taciti sociosqu ad litora torquent ugue. Sed non neque elit. Sed ut imperdiet nisi. Proin condimentum fermentum nunc. Etiam pharetra, imperdiet nisi. Proin condimentum fermentum nunc. Etiam pharetra, erat sed fermentum feugiat, velit mauris egestas quam, ut aliquam massa nisl quis neque. Suspendisse in orci enim.</p>
    <p>This is a sample version of Lorem Ipsum. Proin gravida nibh vel velit auctor aliquet. Aenean sollicitudin, lorem quis bibendum auctor, nisi elit consequat ipsum, nec sagittis sem nibh id elit. Duis sed odio sit amet nibh vulputate cursus a sit amet mauris. Morbi accumsan ipsum velit. Nam nec tellus a odio tincidunt auctor a ornare odio. Sed non mauris vitae erat consequat auctor eu in elit. Class aptent taciti sociosqu ad litora torquent per conubia nostra, per inceptos himenaeos. Mauris in erat justo.</p>
    <p>Nullam ac urna eu felis dapibus condimentum sit amet a augue. Sed non neque elit. Sed ut imperdiet nisi. Proin condimentum fermentum nunc. Etiam pharetra, erat sed fermentum feugiat, velit mauris egestas quam. Nullam ac urna eu felis dapibus condimentum sit amet a aug pharetra, erat sed fermentum feugiat, velit mauris egestas quam. Nullam ac urna eu felis dapibus condimentum sit amet a augue. Sed non neque elit. Sed ut imperdiet nisi. Proin condimentum fermentum nunc.</p>
  </div>

  <div class="closing">
    <p>Sincerely,</p>
    <p class="sender-name">Owen Hartley</p>
  </div>

  <div class="footer-bar-dark"></div>
  <div class="footer-bar-green"></div>
</section>

<section class="email-signature">
  <div class="brand-name">Velmora<br>Cabinets</div>
  <div class="signature-rule"></div>
  <div class="signature-details">
    <p class="person-name">Daniel Ashcroft</p>
    <p class="person-title">Director Craftsman</p>
    <ul class="contact-list">
      <li><svg viewBox="0 0 10 10"><path d="M1 3c0-1.5 1.5-2 4-2s4 .5 4 2v1H7V3H3v1H1zM2.5 5h5l1 4h-7z"/></svg>0412555309</li>
      <li><svg viewBox="0 0 10 10"><path d="M0 2h10v6H0z M0 2l5 3.5L10 2" stroke="#fff" stroke-width=".8"/></svg>info@velmoracabinets.com.au</li>
      <li><svg viewBox="0 0 10 10"><circle cx="5" cy="5" r="4"/></svg>@velmora.cabinets</li>
    </ul>
  </div>
</section>

</body>
</html>
```